Business card design for international hub site

I need a business card design with the logo attached. Although the site is for the teenage audience (it is about the high school graduation ball, the Prom), the business card is for professional use to be given to professional contacts (B2B), such as suppliers and partners, so it needs to look professional (but also girly, glamours and clean).

Target Market(s)

B2B

Industry/Entity Type

Media

Colors
eea4c8
f9d9e8
e667a6
9d9d9d
1b1b1b

Requirements
Must have
• Space for Name, Tile, Address, Phone, email and website.
Should not have
• Photo

```html
<!DOCTYPE html>
<html lang="en">
<head>
<meta charset="utf-8">
<title>The Gala Bloom – Business Card</title>
<link rel="stylesheet" href="https://fonts.googleapis.com/css2?family=EB+Garamond:wght@400;500&family=Pinyon+Script&display=swap">
<style>
  :root {
    --pink-soft: #eea4c8;
    --pink-pale: #f9d9e8;
    --pink-strong: #e667a6;
    --pink-deep: #e0407f;
    --grey: #9d9d9d;
    --ink: #1b1b1b;
    --card: #ffffff;
    --stage: #ececec;
  }
  * { margin: 0; padding: 0; box-sizing: border-box; }
  html, body { width: 1200px; height: 586px; overflow: hidden; }
  body {
    background: var(--stage);
    font-family: "EB Garamond", Georgia, serif;
    position: relative;
  }
  .card {
    position: absolute;
    top: 128px;
    width: 502px;
    height: 301px;
    background: var(--card);
    overflow: hidden;
  }
  .card--front { left: 80px; }
  .card--back { left: 588px; }

  .ornament { position: absolute; top: 0; height: 100%; }
  .card--front .ornament {
    right: 0; width: 240px;
    background: linear-gradient(90deg, rgba(249,217,232,0) 0%, var(--pink-pale) 25%, var(--pink-soft) 65%, var(--pink-strong) 100%);
  }
  .card--back .ornament--main {
    left: 0; width: 180px;
    background: linear-gradient(90deg, var(--pink-strong) 0%, var(--pink-soft) 45%, var(--pink-pale) 75%, rgba(249,217,232,0) 100%);
  }
  .card--back .ornament--faint {
    right: 0; width: 150px;
    background: linear-gradient(90deg, rgba(249,217,232,0) 0%, rgba(249,217,232,0.55) 100%);
  }

  .brand-name {
    position: absolute;
    left: 46px;
    top: 112px;
    width: 200px;
    color: var(--grey);
    font-weight: 400;
    font-size: 46px;
    line-height: 0.9;
  }

  .contact-block {
    position: absolute;
    right: 54px;
    top: 66px;
    text-align: right;
  }
  .person-name {
    font-family: "Pinyon Script", cursive;
    color: var(--pink-strong);
    font-size: 36px;
    font-weight: 400;
    line-height: 1.2;
    margin-bottom: 18px;
    margin-right: -8px;
  }
  .contact-list { list-style: none; }
  .contact-item {
    display: flex;
    justify-content: flex-end;
    align-items: center;
    gap: 10px;
    color: var(--ink);
    font-size: 12.5px;
    height: 24px;
    margin-right: -16px;
  }
  .contact-icon { width: 13px; height: 11px; fill: var(--pink-strong); }
  .address {
    font-style: normal;
    color: var(--pink-strong);
    font-size: 12.5px;
    line-height: 1.5;
    margin-top: 6px;
  }
</style>
</head>
<body>
  <section class="card card--front">
    <h1 class="brand-name">The Gala Bloom</h1>
    <div class="ornament" role="img" aria-label="Pink floral swirl ornament with flowers and curling vines"></div>
  </section>

  <section class="card card--back">
    <div class="ornament ornament--main" role="img" aria-label="Pink floral swirl ornament with flowers and curling vines"></div>
    <div class="ornament ornament--faint" role="img" aria-label="Faint pale pink floral swirl ornament"></div>

    <div class="contact-block">
      <h2 class="person-name">Rosa Marlowe</h2>
      <ul class="contact-list">
        <li class="contact-item">
          <span>+44 (0)1632 960481</span>
          <svg class="contact-icon" viewBox="0 0 13 11" aria-label="Phone"><path d="M1 3.5C1 1.8 3.5 1 6.5 1S12 1.8 12 3.5V4.5H9.5V3.2H3.5V4.5H1Z"/><path d="M3 5.2L4.5 3.8H8.5L10 5.2L11 10H2Z"/></svg>
        </li>
        <li class="contact-item">
          <span>(555) 014-2290</span>
          <svg class="contact-icon" viewBox="0 0 13 11" aria-label="Fax"><rect x="3.5" y="0.5" width="6" height="3"/><rect x="0.5" y="4" width="12" height="4.5" rx="1"/><rect x="3.5" y="8" width="6" height="2.5"/></svg>
        </li>
        <li class="contact-item">
          <span>rosa@thegalabloom.com</span>
          <svg class="contact-icon" viewBox="0 0 13 11" aria-label="Email"><path d="M0.5 1.5H12.5V10H0.5Z M1.5 2.5L6.5 6.5L11.5 2.5" stroke="#fff" stroke-width="0.8"/></svg>
        </li>
      </ul>
      <address class="address">Orchard Row, Ashby<br>Kelton, KL4 2PD</address>
    </div>
  </section>
</body>
</html>
```